New B2C website design to help dads be better dads

DadHarbor is a website to help dads be the “best dad you can be.”

We require our website to be designed into a PSD format, no coding necessary.

The general concept is a two-page design. The first page is the login page, the second page is the home page. Once at the home page, rather than navigating to and from different pages, the user will push and pull through different visual and functional layers of the hierarchy. In theory, this should add to the user experience by having a visual anchor of where they are (through layered pagination) as well as improving loading times since the new information should only be a delta in data load versus a brand new page load.

The general look-and-feel we are going for is clean, simple, minimal. This means that the winning design will show us a good eye for web-optimized typography, good use of white (negative) space, and good use of a visually pleasing grid.

We require a total of 6 page "views" plus the landing page. We note that many of the views are similar to one another.
Landing page
Milestone view
Task view
Content view, articles
Content view, products
Search view
What's new view

Please review all of the additional information provided as well as the attachments for examples.

We provide the following websites as good references for:

Typography:
http://example-kelvorn.com/journal/

Use of white space:
http://www.trenvaskit.com/
http://moldrefin.com/

Example for “scrolling” page concept as well as good balance of color, typography, and white space:
http://www.qorbitalmeet.eu/

Please contact us with questions so that we can guide your design effort.
Updates

Hello designers,

The following information is added to help guide the design process:

1.  For the text dialogue below the landing page, please assume the following word count:
"why are we making dad harbor?": 250 words
"who are we?" 200 words
"what's the deal with the penguin logo?" 300 words

For the social media links, please see http://www.gravelplumbs.com/
Notice the floating "social" bar that is always to the right.  This is the concept we are going for, please try to implement this as you see fit. 

Target Market(s)

Fathers of young children ages 0-6 years old.

Industry/Entity Type

Product

Font styles to use
Sans Serif

Requirements
Must have
• Clean lines, minimal design concept

Incorporation of our logo (see attached document)

Header content is static for all views after landing page, see example

This page WILL be responsive, please keep that in mind when designing
The timeline bar should be to the left, with the timeline bar’s “milestones” also being responsive.

Designer is free to suggest font types, but any fonts used must be royalty-free and web-optimized. We request a minimum number of font types as well as fonts that load relatively fast. We reinforce that visually appealing typography is a significant factor in the winning design choice.

While we are not expecting the winning design to include code, please keep in mind that the final implementation needs to be optimized for desktop, tablet, and mobile platforms.

If you are using stock photography that is not generated by you, please provide where/how we can obtain imagery, as well as price.

All custom graphics must be available in original formats; Photoshop/GIMP layered files for layout design, and vector formats for logos, icons and other graphical elements.

Please incorporate “Blue” into design elements as you see fit, as the RGB 67 74 169 Blue is the primary color used in our brand. The complement to this blue is 255 202 0, a brownish orange. Feel free to use this color as well, although please keep it to a lesser amount.

Background color is your choice, do not feel the need to use the grey.
Should not have
• Excessive graphical content such that it affects loading times

Excessive use of too many font types such that it affects loading times

```html
<!DOCTYPE html>
<html lang="en">
<head>
<meta charset="utf-8">
<title>DadHarbor</title>
<link rel="stylesheet" href="https://fonts.googleapis.com/css2?family=Cutive+Mono&family=Roboto:ital,wght@0,300;0,400;0,500;1,400&display=swap">
<style>
  :root {
    --brand-blue: #434aa9;
    --brand-yellow: #ffca00;
    --yellow-edge: #d9a800;
    --ink: #333333;
    --muted: #555555;
    --rule: #cfcfcf;
    --footer-bg: #ebebeb;
    --icon-grey: #9a9a9a;
    --field-border: #cccccc;
    --sky-top: #6f9ddf;
    --sky-low: #b3d0f1;
    --grass: #7a7a45;
    --grass-dark: #5d5a34;
  }
  * { box-sizing: border-box; margin: 0; padding: 0; }
  html, body { width: 932px; height: 1200px; overflow: hidden; background: #fff; }
  body { position: relative; font-family: "Roboto", Arial, sans-serif; color: var(--ink); }

  .site-header { position: absolute; top: 0; left: 0; width: 932px; height: 126px; }
  .brand { position: absolute; left: 100px; top: 48px; display: flex; align-items: center; gap: 8px; }
  .brand-dot { width: 22px; height: 22px; border-radius: 50%; background: var(--brand-blue); }
  .brand-name { font-family: "Roboto", Arial, sans-serif; font-weight: 500; font-size: 22px; color: var(--brand-blue); }

  .login { position: absolute; left: 586px; top: 18px; width: 246px; }
  .login-title { font-size: 14px; font-weight: 400; color: var(--brand-blue); letter-spacing: .5px; }
  .login-fields { display: flex; gap: 10px; margin-top: 8px; }
  .login-field { width: 118px; height: 24px; border: 1px solid var(--field-border); border-radius: 2px; font: 400 10px "Roboto", sans-serif; color: #999; padding: 0 9px; display: flex; align-items: center; }
  .login-actions { display: flex; justify-content: flex-end; align-items: center; margin-top: 10px; gap: 10px; }
  .login-links { font-size: 8.5px; font-style: italic; color: var(--brand-blue); }
  .btn-signin { width: 66px; height: 30px; background: var(--brand-yellow); border-bottom: 2px solid var(--yellow-edge); font-size: 10px; font-weight: 500; color: #222; display: flex; align-items: center; justify-content: center; border-radius: 2px; }

  .hero { position: absolute; top: 126px; left: 0; width: 932px; height: 404px;
    background: linear-gradient(180deg, var(--sky-top) 0%, var(--sky-low) 62%, var(--grass) 67%, var(--grass-dark) 100%); }
  .hero-cta { position: absolute; left: 334px; top: 299px; width: 264px; height: 45px; background: var(--brand-yellow); border-bottom: 3px solid var(--yellow-edge); font-size: 17px; color: #222; display: flex; align-items: center; justify-content: center; }
  .hero-scroll { position: absolute; left: 444px; top: 327px; width: 44px; height: 44px; border-radius: 50%; background: var(--brand-blue); display: flex; align-items: center; justify-content: center; }

  .about-title { position: absolute; top: 560px; left: 0; width: 932px; text-align: center; font-size: 32px; font-weight: 300; color: #333; }
  .about-section { position: absolute; left: 101px; width: 730px; }
  .about-heading { font-family: "Cutive Mono", "Courier New", monospace; font-size: 20px; color: var(--brand-blue); letter-spacing: 2px; font-weight: 400; }
  .about-heading .initial { font-size: 28px; letter-spacing: 0; }
  .about-body { font-size: 10px; font-weight: 300; line-height: 18px; color: var(--ink); margin-top: 10px; }
  .divider { position: absolute; left: 101px; width: 730px; height: 1px; background: var(--rule); }

  .logo-story { display: flex; gap: 13px; margin-top: 8px; }
  .logo-story-mark { flex: 0 0 77px; height: 70px; display: flex; flex-direction: column; align-items: center; justify-content: center; gap: 6px; }
  .logo-story-mark .brand-dot { width: 16px; height: 16px; }
  .logo-story-mark .brand-name { font-size: 12px; }
  .logo-story .about-body { margin-top: 0; }

  .site-footer { position: absolute; left: 0; top: 1116px; width: 932px; height: 84px; background: var(--footer-bg); }
  .copyright { position: absolute; left: 100px; top: 36px; font-size: 10px; font-weight: 300; color: var(--muted); }
  .copyright .brand-link { color: var(--brand-blue); font-weight: 400; }
  .social { position: absolute; left: 724px; top: 28px; display: flex; gap: 10px; }
  .social-dot { width: 28px; height: 28px; border-radius: 50%; background: var(--icon-grey); }
</style>
</head>
<body>
  <header class="site-header">
    <div class="brand"><span class="brand-dot"></span><span class="brand-name">DadHarbor</span></div>
    <form class="login">
      <div class="login-title">LOG IN</div>
      <div class="login-fields">
        <div class="login-field">Username</div>
        <div class="login-field">Password</div>
      </div>
      <div class="login-actions">
        <span class="login-links">Forgot Login? &nbsp;| &nbsp;Request Access</span>
        <div class="btn-signin">SIGN IN</div>
      </div>
    </form>
  </header>

  <section class="hero" role="img" aria-label="Photo of a father lying in a grassy field under a blue sky, lifting his young son into the air">
    <div class="hero-cta">Learn About Dad Harbor</div>
    <div class="hero-scroll">
      <svg width="16" height="10" viewBox="0 0 16 10"><path d="M2 2 L8 8 L14 2" fill="none" stroke="#fff" stroke-width="2.5" stroke-linecap="round" stroke-linejoin="round"/></svg>
    </div>
  </section>
  <div class="hero-cta" style="top:425px;z-index:2">Learn About Dad Harbor</div>

  <h1 class="about-title">About Dad Harbor</h1>

  <section class="about-section" style="top:632px">
    <h2 class="about-heading"><span class="initial">W</span>hy are we making Dad Harbor?</h2>
    <p class="about-body">Lorem ipsum dolor sit amet, consectetur adipisicing elit, sed do eiusmod tempor incididunt ut labore et dolore magna aliqua. Ut enim ad minim veniam, quis nostrud exercitation ullamco laboris nisi ut aliquip ex ea commodo consequat. Duis aute irure dolor in reprehenderit in voluptate velit esse cillum dolore eu fugiat nulla pariatur. Excepteur sint occaecat cupidatat non proident, sunt in culpa qui officia deserunt mollit anim id est laborum.<br>Aliquam molestie, mi et imperdiet euismod, dui purus auctor tellus, et interdum lacus lectus et ante. Sed accumsan sollicitudin sapien, sit amet adipiscing turpis gravida ac. In congue, neque ac lobortis volutpat, libero mauris varius mi, vitae suscipit ipsum ligula vitae risus.</p>
  </section>
  <div class="divider" style="top:788px"></div>

  <section class="about-section" style="top:809px">
    <h2 class="about-heading"><span class="initial">W</span>ho are we?</h2>
    <p class="about-body">Lorem ipsum dolor sit amet, consectetur adipisicing elit, sed do eiusmod tempor incididunt ut labore et dolore magna aliqua. Ut enim ad minim veniam, quis nostrud exercitation ullamco laboris nisi ut aliquip ex ea commodo consequat. Duis aute irure dolor in reprehenderit in voluptate velit esse cillum dolore eu fugiat nulla pariatur. Excepteur sint occaecat cupidatat non proident, sunt in culpa qui officia deserunt mollit anim id est laborum.<br>Aliquam molestie, mi et imperdiet euismod, dui purus auctor tellus, et interdum lacus lectus et ante. Sed accumsan sollicitudin sapien, sit amet adipiscing turpis gravida ac. In congue, neque ac lobortis volutpat, libero mauris varius mi, vitae suscipit ipsum ligula vitae risus.</p>
  </section>
  <div class="divider" style="top:966px"></div>

  <section class="about-section" style="top:984px">
    <h2 class="about-heading"><span class="initial">W</span>hat’s the deal with the Penguin logo?</h2>
    <div class="logo-story">
      <div class="logo-story-mark"><span class="brand-dot"></span><span class="brand-name">DadHarbor</span></div>
      <p class="about-body">Lorem ipsum dolor sit amet, consectetur adipisicing elit, sed do eiusmod tempor incididunt ut labore et dolore magna aliqua. Ut enim ad minim veniam, quis nostrud exercitation ullamco laboris nisi ut aliquip ex ea commodo consequat. Duis aute irure dolor in reprehenderit in voluptate velit esse cillum dolore eu fugiat nulla pariatur. Excepteur sint occaecat cupidatat non proident, sunt in culpa qui officia deserunt mollit anim id est laborum.</p>
    </div>
  </section>

  <footer class="site-footer">
    <p class="copyright">Copyright © 2013. <span class="brand-link">Dad Harbor</span>. All Right Reserved</p>
    <div class="social" aria-label="Social links">
      <span class="social-dot"></span>
      <span class="social-dot"></span>
      <span class="social-dot"></span>
    </div>
  </footer>
</body>
</html>
```